HOT TUB - SPAS service needs an business card

I need an business for my company who his specialise in a maintenance,water treatment and cleaning of Hot Tub - Spas for commercial and residential customers. The company operate mainly in the ski resort of Chamonix, Megève and St Gervais. The final product should communicate pure water, cleanest and professional for luxury property's.
I have upload a logo but any improvement on it is welcome.(color,size, details etc..) or any other idea. Thank you
Company Name: 58 BAINS
My name: Lucien Marchetti
Email: lucimarch@examplemail.net
Tel: +33 (0)6 71 58 29 64
Description to be on the card in french(first langage) and in English:
- Spas service
- Entretien, traitement eau, nettoyage.
- Maintenance, water treatment, cleaning.
Industry/Entity Type
Residential
Colors
Designer to choose colors to be used in the design.
Look and feel
Each slider illustrates characteristics of the customer's brand and the style your logo design should communicate.

```html
<!DOCTYPE html>
<html lang="fr">
<head>
<meta charset="utf-8">
<title>58 BAINS – Business Card</title>
<link rel="stylesheet" href="https://fonts.googleapis.com/css2?family=Source+Sans+3:wght@400;600;700&display=swap">
<style>
  :root {
    --page-bg: #eef1f4;
    --card-front: #1fa3f5;
    --card-back: #0b78d8;
    --ink: #ffffff;
    --rule: rgba(255, 255, 255, 0.75);
  }
  * { margin: 0; padding: 0; box-sizing: border-box; }
  html, body {
    width: 1200px;
    height: 1120px;
    overflow: hidden;
    background: var(--page-bg);
    font-family: "Source Sans 3", "Myriad Pro", Arial, sans-serif;
    color: var(--ink);
  }
  .canvas { position: relative; width: 1200px; height: 1120px; }

  .card {
    position: absolute;
    width: 874px;
    height: 499px;
    border-radius: 38px;
    text-align: center;
  }
  .card--front { left: 30px; top: 17px; background: var(--card-front); }
  .card--back  { left: 293px; top: 563px; background: var(--card-back); }

  .brand-mark {
    position: absolute;
    left: 0; right: 0;
    display: flex;
    align-items: center;
    justify-content: center;
    gap: 16px;
    font-weight: 600;
    font-size: 46px;
    letter-spacing: 2px;
  }
  .brand-mark__dot {
    width: 16px; height: 16px;
    border-radius: 50%;
    background: var(--ink);
  }
  .card--front .brand-mark { top: 128px; }
  .card--back .brand-mark { top: 150px; }

  .company-name {
    position: absolute;
    left: 0; right: 0;
    top: 270px;
    font-size: 40px;
    font-weight: 600;
    line-height: 1;
  }
  .divider {
    position: absolute;
    left: 58px;
    width: 740px;
    top: 334px;
    height: 4px;
    border-radius: 50%;
    background: linear-gradient(90deg, rgba(255,255,255,0) 0%, var(--rule) 15%, var(--rule) 85%, rgba(255,255,255,0) 100%);
  }
  .person-name {
    position: absolute;
    left: 0; right: 0;
    top: 358px;
    font-size: 30px;
    font-weight: 700;
    line-height: 1;
    padding-right: 20px;
  }
  .contact {
    position: absolute;
    left: 0; right: 0;
    display: flex;
    align-items: center;
    justify-content: center;
    gap: 10px;
    font-size: 28px;
    font-weight: 600;
    line-height: 1;
  }
  .contact--phone { top: 409px; padding-right: 20px; }
  .contact--email { top: 455px; font-weight: 400; padding-right: 20px; }
  .contact__icon { width: 24px; height: 24px; flex: none; }

  .services-title {
    position: absolute;
    left: 0; right: 0;
    top: 349px;
    font-size: 32px;
    font-weight: 700;
    line-height: 1;
  }
  .services-list {
    position: absolute;
    left: 0; right: 0;
    list-style: none;
    display: flex;
    justify-content: center;
    gap: 14px;
    font-size: 31px;
    line-height: 1;
  }
  .services-list li::before { content: "•"; margin-right: 4px; }
  .services-list--fr { top: 402px; }
  .services-list--en { top: 444px; }
</style>
</head>
<body>
<main class="canvas">

  <section class="card card--front" aria-label="Recto de la carte">
    <div class="brand-mark"><span class="brand-mark__dot"></span>58 BAINS</div>
    <h1 class="company-name">58 BAINS</h1>
    <div class="divider"></div>
    <p class="person-name">Lucien Marchetti</p>
    <p class="contact contact--phone">
      <svg class="contact__icon" viewBox="0 0 24 24" aria-hidden="true">
        <path d="M6.6 2.5c.6-.3 1.2 0 1.5.5l2 3.6c.3.6.1 1.2-.4 1.6l-1.5 1c.9 2.3 2.4 4.1 4.5 5.5l1.2-1.4c.4-.5 1.1-.6 1.6-.3l3.5 2.2c.5.3.7 1 .4 1.5l-1.2 2.4c-.4.8-1.3 1.2-2.2 1-6.2-1.6-10.5-6.6-11.6-13-.2-.9.3-1.8 1.1-2.2z" fill="none" stroke="#fff" stroke-width="1.8" stroke-linejoin="round"/>
      </svg>
      +33 (0)6 71 58 29 64
    </p>
    <p class="contact contact--email">
      <svg class="contact__icon" viewBox="0 0 24 24" aria-hidden="true">
        <path d="M2 10 12 3l10 7v10H2z" fill="#fff"/>
        <path d="M2 10l10 6 10-6" fill="none" stroke="#1fa3f5" stroke-width="1.6"/>
      </svg>
      lucimarch@examplemail.net
    </p>
  </section>

  <section class="card card--back" aria-label="Verso de la carte">
    <div class="brand-mark"><span class="brand-mark__dot"></span>58 BAINS</div>
    <h2 class="services-title">SPAS SERVICES</h2>
    <ul class="services-list services-list--fr" lang="fr">
      <li>Entretien</li>
      <li>traitement eau</li>
      <li>nettoyage</li>
    </ul>
    <ul class="services-list services-list--en" lang="en">
      <li>Maintenance</li>
      <li>water treatment</li>
      <li>cleaning.</li>
    </ul>
  </section>

</main>
</body>
</html>
```